Veltrona Pocket Folder

Create a new pocket folder
An Overview / Background of the Business & Services
We would like a new folder to use when making formal presentations
* The Target Market / Audience you are trying to reach
The target audience are commercial businesses that we are selling group insurance products to
* Design Specifics; any preferences or ideas for Style, Colour, Imagery, etc
We wanted to use the Houston, Texas skyline and create something that was simple, yet modern.
* Do you have an existing website or Facebook page were designers can learn more about your company?
Yes, http://www.veltronagroup.example and we are on Linked-In.
Updates
Project Deadline Extended Reason: We have many people who have to agree. We need to get an answer on the form of the ready art we will receive when we select a designer .Thank you. Added Thursday, April 27, 2017
Industry/Entity Type
Business
Look and feel
Each slider illustrates characteristics of the customer's brand and the style your logo design should communicate.

```html
<!DOCTYPE html>
<html lang="en">
<head>
<meta charset="utf-8">
<title>Veltrona Pocket Folder</title>
<link rel="stylesheet" href="https://fonts.googleapis.com/css2?family=Open+Sans:wght@400;600;700&display=swap">
<style>
  :root {
    --stage: #bdbdbd;
    --blue-light: #35a9e0;
    --blue-mid: #1b8ccc;
    --blue-deep: #0b6aa6;
    --paper: #ffffff;
    --paper-shade: #ececec;
    --logo-grey: #58595b;
    --logo-blue: #1f8fd2;
    --skyline: #d3d6d9;
    --skyline-deep: #c4c7ca;
    --contact-text: rgba(255, 255, 255, 0.88);
    --icon-cut: #1179b8;
  }
  * { margin: 0; padding: 0; box-sizing: border-box; }
  html, body {
    width: 1200px;
    height: 828px;
    overflow: hidden;
    background: var(--stage);
    font-family: "Open Sans", Arial, sans-serif;
  }
  .folder-spread {
    position: absolute;
    left: 60px;
    top: 34px;
    width: 1080px;
    height: 760px;
    display: flex;
  }
  .back-cover {
    position: relative;
    width: 540px;
    height: 100%;
    background:
      radial-gradient(ellipse 70% 55% at 30% 20%, rgba(255,255,255,0.14), transparent 70%),
      linear-gradient(160deg, var(--blue-light) 0%, var(--blue-mid) 50%, var(--blue-deep) 100%);
  }
  .back-cover__glow {
    position: absolute;
    inset: 0;
    background: linear-gradient(200deg, rgba(255,255,255,0.08) 0%, transparent 45%);
  }
  .contact-block {
    position: absolute;
    left: 46px;
    bottom: 46px;
    color: var(--contact-text);
    font-size: 10.5px;
    font-style: normal;
    line-height: 1.45;
  }
  .contact-block__company { font-weight: 700; }
  .contact-list {
    list-style: none;
    margin-top: 12px;
  }
  .contact-list li {
    display: flex;
    align-items: center;
    gap: 9px;
    margin-bottom: 3px;
  }
  .contact-list svg { width: 10px; height: 10px; fill: var(--contact-text); flex: none; }
  .front-cover {
    position: relative;
    width: 540px;
    height: 100%;
    background: linear-gradient(200deg, var(--paper) 0%, var(--paper) 45%, var(--paper-shade) 100%);
  }
  .brand {
    position: absolute;
    left: 58px;
    top: 180px;
    display: flex;
    align-items: center;
    gap: 12px;
  }
  .brand__mark {
    width: 54px;
    height: 54px;
    background: var(--logo-blue);
    border-radius: 6px;
  }
  .brand__name {
    font-size: 46px;
    font-weight: 700;
    line-height: 1;
    color: var(--logo-grey);
    letter-spacing: 0.5px;
  }
  .skyline {
    position: absolute;
    left: 0;
    bottom: 0;
    width: 100%;
    height: 150px;
    background: linear-gradient(180deg, rgba(211,214,217,0.55) 0%, var(--skyline) 35%, var(--skyline-deep) 100%);
  }
</style>
</head>
<body>
  <main class="folder-spread">
    <section class="back-cover">
      <div class="back-cover__glow"></div>
      <address class="contact-block">
        <p class="contact-block__company">Veltrona Agency LLC</p>
        <p>2450 Westmere Drive, Suite 410</p>
        <p>Carrow Bay, Delmont, 30418</p>
        <ul class="contact-list">
          <li>
            <svg viewBox="0 0 10 10" aria-hidden="true"><path d="M2 0.5 L3.6 2.6 L2.8 3.6 Q3.8 5.8 6.4 7.2 L7.4 6.4 L9.5 8 L8.6 9.5 Q4.5 9.3 0.5 1.4 Z"/></svg>
            <span>555-010-0148</span>
          </li>
          <li>
            <svg viewBox="0 0 10 10" aria-hidden="true"><path d="M0.5 2 H9.5 V8 H0.5 Z M1 2.4 L5 5.4 L9 2.4" stroke="var(--icon-cut)" stroke-width="0.6"/></svg>
            <span>info@veltronagroup.example</span>
          </li>
          <li>
            <svg viewBox="0 0 10 10" aria-hidden="true"><circle cx="5" cy="5" r="4.5"/><path d="M0.5 5 H9.5 M5 0.5 V9.5" stroke="var(--icon-cut)" stroke-width="0.6"/></svg>
            <span>www.veltronagroup.example</span>
          </li>
        </ul>
      </address>
    </section>
    <section class="front-cover">
      <div class="brand">
        <div class="brand__mark"></div>
        <span class="brand__name">Veltrona</span>
      </div>
      <div class="skyline" role="img" aria-label="Soft grey silhouette of a city skyline"></div>
    </section>
  </main>
</body>
</html>
```